Hard-File Archival Services Billboard (Digitization Service) for Attorneys/Law Firms

I need a billboard design for my company "Velkor Legal Aides" that advertises our primary service: Digitization of closed client files, for law firms and attorneys. Our system works as follows: 1) We get a call about a firm that wants to digitize their archived (closed) client files (which usually find their way to file cabinets or bankers boxes), 2) We go and pick those up from the law firm, 3) We bring them to our digitization facility, scan them in, and convert them into searchable PDF/A files, and 4) We upload them on the cloud, give the client a URL to visit their files whenever they want, and we delete them when requested by the client (usually for the retention duration for Missouri's rules of professional conduct, which is 6 years). It would be really cool to see "Velkor Legal Aides" and the logo clearly on the billboard, some simple sentence relating to "Missouri's best digitizing and cloud storage service for closed client files for attorneys" (or something shorter, you get the point), with maybe a linear set of photos and arrows (as follows 1. A photo of a file cabinet opened with files hanging out of it, 2. an arrow pointing to a person scanning in documents in a big scanner (maybe with a Velkor Legal Aidez logo on it?), 3. An arrow pointing to a "secure" appearing cloud (representing cloud storage), and 4. the client sitting at a computer with an arrow pointing back to the cloud (showing the client is accessing the cloud files through the computer). Our website is www.velkorlegalaides.example if you want to glean any additional information from there. Thanks! Oh yes, I should also say the billboard dimensions (in the event you need this for photo aspect ratio) will be as follows: 14 feet tall by 48 feet wide.
Target Market(s)
Attorneys in Springfield, Missouri
Industry/Entity Type
Legal
Look and feel

```html
<!DOCTYPE html>
<html lang="en">
<head>
<meta charset="utf-8">
<title>Velkor Legal Aides Billboard</title>
<link rel="stylesheet" href="https://fonts.googleapis.com/css2?family=Montserrat:wght@400;700&family=Roboto+Condensed:wght@700&display=swap">
<style>
  :root {
    --navy: #2b3a9c;
    --cloud: #4f63b3;
    --peach: #f6cdb4;
    --peach-band: #f4c7ab;
    --white: #ffffff;
    --stage: #e8ecf2;
  }
  * { margin: 0; padding: 0; box-sizing: border-box; }
  html, body { width: 1200px; height: 756px; overflow: hidden; background: var(--stage); }
  .canvas { position: relative; width: 1200px; height: 756px; }
  .billboard {
    position: absolute; left: 0; top: 203px; width: 1200px; height: 350px;
    overflow: hidden;
    background: linear-gradient(180deg, var(--peach) 0%, #fbe6da 30%, var(--white) 58%);
  }
  .hero-illustration {
    position: absolute; left: 18px; top: 22px; width: 468px; height: 280px;
    border-radius: 140px;
    background: linear-gradient(135deg, var(--cloud) 0%, var(--navy) 100%);
  }
  .portrait {
    position: absolute; left: 40px; top: 42px; width: 280px; height: 308px;
    border-radius: 140px 140px 0 0;
    background: linear-gradient(180deg, #c9a08a 0%, #e9b79d 45%, #d9a78e 100%);
  }
  .corner-badge {
    position: absolute; left: 1038px; top: -66px; width: 224px; height: 224px;
    border-radius: 50%; background: var(--navy);
  }
  .corner-name {
    position: absolute; left: 1062px; top: 52px; width: 130px;
    font-family: "Montserrat", sans-serif; font-weight: 700; font-size: 17px;
    line-height: 21px; color: var(--white); text-align: center;
  }
  .brand-name {
    position: absolute; left: 512px; top: 104px;
    font-family: "Montserrat", sans-serif; font-weight: 700; font-size: 56px;
    color: var(--navy); letter-spacing: 0.5px; white-space: nowrap;
  }
  .tagline {
    position: absolute; left: 514px; top: 190px; width: 620px;
    font-family: "Montserrat", sans-serif; font-weight: 400; font-size: 25px;
    line-height: 36px; color: var(--navy);
  }
  .contact-web {
    position: absolute; left: 420px; top: 290px; width: 470px; height: 60px;
    border-radius: 30px 0 0 30px; background: var(--navy);
    display: flex; align-items: center; padding-left: 26px; gap: 14px;
  }
  .contact-phone {
    position: absolute; left: 850px; top: 290px; width: 350px; height: 60px;
    border-radius: 30px 0 0 30px; background: var(--peach-band);
    display: flex; align-items: center; padding-left: 30px; gap: 12px;
  }
  .contact-text {
    font-family: "Roboto Condensed", sans-serif; font-weight: 700; font-size: 31px;
    white-space: nowrap;
  }
  .contact-web .contact-text { color: var(--white); }
  .contact-phone .contact-text { color: var(--navy); }
</style>
</head>
<body>
<div class="canvas">
  <section class="billboard">
    <div class="hero-illustration" role="img" aria-label="Illustration of blue clouds with upload and download arrows"></div>
    <div class="portrait" role="img" aria-label="Photo of a smiling young man in a peach sweater holding a laptop"></div>
    <div class="corner-badge"></div>
    <p class="corner-name">Velkor Legal Aides</p>
    <h1 class="brand-name">Velkor Legal Aides</h1>
    <p class="tagline">Missouri's best digitizing and cloud storage service for closed client files for attorneys</p>
    <div class="contact-web">
      <svg width="26" height="26" viewBox="0 0 26 26" aria-hidden="true">
        <circle cx="13" cy="13" r="11" fill="none" stroke="#fff" stroke-width="2.4"/>
        <ellipse cx="13" cy="13" rx="4.5" ry="11" fill="none" stroke="#fff" stroke-width="2"/>
        <line x1="2" y1="13" x2="24" y2="13" stroke="#fff" stroke-width="2"/>
      </svg>
      <span class="contact-text">velkorlegalaides.example</span>
    </div>
    <div class="contact-phone">
      <svg width="22" height="22" viewBox="0 0 24 24" aria-hidden="true">
        <path fill="var(--navy)" d="M6.6 10.8a15.1 15.1 0 0 0 6.6 6.6l2.2-2.2a1 1 0 0 1 1-.25 11.4 11.4 0 0 0 3.6.57 1 1 0 0 1 1 1V20a1 1 0 0 1-1 1A17 17 0 0 1 3 4a1 1 0 0 1 1-1h3.5a1 1 0 0 1 1 1c0 1.25.2 2.45.57 3.57a1 1 0 0 1-.25 1z"/>
      </svg>
      <span class="contact-text">+1 (417) 555-0143</span>
    </div>
  </section>
</div>
</body>
</html>
```